Radical T-shirt Company Shopify Site

I would like to have a a Shopify site designed (and built) for my new t-shirt company. The company is called Zest Crew and will feature t-shirt designs focused on different characters doing extreme sports. The brand has a mellow and slightly comical feel. We will feature different artists designs as different collections of the brand.
We do not have a logo yet, but we do have some of the sample designs from the artists that we will be featuring on the site. This will give a feel for the branding and style of the site. As far as colors go, I am not sure if a dark theme or light theme will be best. Please use your best judgement for initial designs. Our t-shirt designs are simple and typically line-art style.
It is important to keep in mind that we have several artists that we will feature and that we want to showcase all of them equally until we can understand which will be most popular. Our sites should speak to audiences of all ages. Light, mellow, and slightly comical describe our brand. The site should catch the audiences eye and allow them to see multiple products so they are more likely to buy multiple products.

Expected deliverables:
1. Zest Crew Outfitters website (focused on mobile device viewing)- including landing page, multiple collections, product pages, variable colors and sized for shirts and other products, about page, contact page, cart with upsells, subscription package functionality, mailing list pop-up, chat support widget, promo codes, payment collection via stripe- All features should be tested and functioning properly before launch. The site must also be set up to A/B test different products, variations, and upsells.
2. Zest Nana Website (Focused on mobile site viewing) - Should follow the same branding (with a different logo but in the same coloring and style as the Zest Crew). This should essentially be a copy of the Zest Crew website include landing page, multiple collections, product pages, variable colors and sized for shirts and other products, about page, contact page, cart with upsells, subscription package functionality, mailing list pop-up, chat support widget, promo codes, payment collection via stripe- Again, this is a duplicate of the Zest Crew website, but with a different landing page tuned to Zest Nana gear.
3. Coding and development of these sites - with the input of 20-30 products (images, descriptions, pricing provided)

I will provide:
1. Examples of products to help with branding and design of the site
2. Feedback on the site
3. All product information for addition to the site
4. Shopify and plugin credentials or access as needed
5. Ongoing work if this goes well

Looking forward to seeing everyone's designs!

Target Market(s)

People that would wear shirts with our characters; grandmas, grandpas, moms, dads, kids, pet lovers- pretty much anyone who enjoys a bit of humor and a nice shirt.

Industry/Entity Type

Comical yet high end t-shirts

Coding

Coded - Design and coding required

Font styles to use
Sans Serif

Requirements
Must have
• Mobile device optimized, Collections carousel on landing page, upsells, features, other recent order popups for users viewing the site, mailing list popup, coupon codes
Nice to have
• Elegant yet playful feel, branding that instills trust and a quick buy.

```html
<!DOCTYPE html>
<html lang="en">
<head>
<meta charset="utf-8">
<title>Zest Crew Outfitters – Website Concepts</title>
<link href="https://fonts.googleapis.com/css2?family=Anton&family=Lato:wght@400;700&family=Poppins:wght@400;500;600&display=swap" rel="stylesheet">
<style>
:root{
  --sky:#b4dbea;
  --ink:#111111;
  --text:#333333;
  --muted:#666666;
  --white:#ffffff;
  --wave-light:#e6f1f5;
  --wave-mid:#cfe5ee;
  --accent:#6aaed0;
  --accent-deep:#4f97bd;
  --section-grey:#e8eef2;
  --shot-bg:#dcedf5;
  --bar:#2a2233;
  --blob:#e3e3e6;
  --footer:#000000;
  --footer-text:#bdbdbd;
}
*{box-sizing:border-box;margin:0;padding:0}
html,body{width:726px;height:1200px;overflow:hidden;background:var(--sky)}
.board{position:relative;width:1490px;height:2464px;transform:scale(.48725);transform-origin:0 0;background:var(--sky);font-family:'Lato',sans-serif;color:var(--text)}
.screen{position:absolute;width:683px;overflow:hidden;background:var(--white)}
.screen--mobile{left:36px;top:33px;height:487px}
.screen--home{left:36px;top:566px;height:1850px}
.screen--popup{left:770px;top:33px;height:1850px}

/* shared type */
.display{font-family:'Anton',sans-serif;color:var(--ink);font-weight:400;line-height:1}
.pill{display:inline-flex;align-items:center;justify-content:center;height:25px;padding:0 10px;border:1.5px solid var(--ink);border-radius:14px;font-family:'Poppins',sans-serif;font-weight:600;font-size:9px;color:var(--ink);background:var(--white);white-space:nowrap}
.pill--solid{background:var(--ink);color:var(--white)}

/* wordmark */
.wordmark{font-family:'Anton',sans-serif;color:var(--ink);text-transform:uppercase;line-height:1.05;text-align:center}

/* mobile landing */
.mobile-blob{position:absolute;left:0;top:0}
.mobile-brand{position:absolute;left:62px;top:30px;width:90px;font-size:16px}
.burger{position:absolute;left:598px;top:40px;width:20px;height:16px;display:flex;flex-direction:column;justify-content:space-between}
.burger span{height:3px;background:var(--ink);border-radius:1px}
.mobile-kicker{position:absolute;left:64px;top:152px;font-size:17px;color:#444}
.mobile-title{position:absolute;left:63px;top:184px;font-size:45px;color:#3a3a3a;line-height:1.15}
.mobile-actions{position:absolute;left:63px;top:311px;display:flex;gap:9px}
.mobile-art{position:absolute;left:301px;top:163px;width:303px;height:241px;background:
  radial-gradient(circle at 72% 55%,rgba(255,250,225,.95) 0 9%,rgba(255,240,200,0) 22%),
  radial-gradient(ellipse 20% 42% at 50% 58%,rgba(70,35,35,.55) 0,rgba(70,35,35,0) 100%),
  linear-gradient(180deg,#d88da2 0%,#eab48e 42%,#f1dc90 62%,#8fc3a2 66%,#efe07a 72%,#f3e27e 100%)}
.slider-bar{position:absolute;left:0;bottom:0;width:683px;height:37px;background:var(--bar)}
.slider-bar svg{position:absolute;left:0;top:0}

/* site header */
.site-header{position:absolute;left:0;top:0;width:683px;height:72px;background:var(--white);z-index:2}
.brand-tab{position:absolute;left:52px;top:0;width:105px;height:92px;border-radius:0 0 52px 52px;background:var(--white);z-index:3;display:flex;align-items:center;justify-content:center;padding-top:4px}
.brand-tab .wordmark{font-size:14px}
.nav{position:absolute;left:214px;top:36px;display:flex;gap:24px;font-size:9px;letter-spacing:.3px;color:var(--text);text-transform:uppercase}
.nav-tools{position:absolute;left:557px;top:32px;display:flex;align-items:center;gap:10px;font-size:8px}
.nav-tools .sep{width:1px;height:11px;background:#555}

/* hero */
.hero{position:absolute;left:0;top:72px;width:683px;height:341px;background:
  radial-gradient(ellipse 30% 45% at 82% 40%,rgba(90,160,150,.35) 0,rgba(90,160,150,0) 100%),
  radial-gradient(ellipse 40% 30% at 30% 85%,rgba(255,255,255,.8) 0,rgba(255,255,255,0) 100%),
  linear-gradient(115deg,var(--wave-light) 0%,#f1f6f8 38%,var(--wave-mid) 70%,#b6d9e5 100%)}
.hero-title{position:absolute;left:62px;top:104px;font-size:34px}
.hero-copy{position:absolute;left:63px;top:162px;width:290px;font-size:8.6px;line-height:14.5px;color:var(--text)}
.hero-cta{position:absolute;left:63px;top:209px}
.hero-ring{position:absolute;left:360px;top:61px;width:216px;height:216px;border-radius:50%;border:1.5px solid #a9b8c0}
.hero-disc{position:absolute;left:374px;top:75px;width:188px;height:188px;border-radius:50%;background:radial-gradient(ellipse 42% 50% at 50% 54%,#ffffff 0,#ffffff 55%,rgba(255,255,255,0) 100%),var(--accent)}
.dots{position:absolute;display:flex;gap:4px}
.dots i{width:5px;height:5px;border-radius:50%;background:#c9c9c9}
.dots i.on{background:var(--ink)}

/* about */
.about{position:absolute;left:0;top:413px;width:683px;height:240px;background:var(--white);text-align:center}
.section-title{font-size:22px;text-transform:uppercase}
.about .section-title{margin-top:48px}
.about p{width:450px;margin:18px auto 0;font-size:8.6px;line-height:14.6px;color:var(--text)}
.about .pill{margin-top:18px;width:70px}

/* products */
.products{position:absolute;left:0;top:653px;width:683px;height:642px;background:var(--section-grey);text-align:center}
.products .section-title{margin-top:50px}
.grid{position:absolute;left:63px;top:101px;display:grid;grid-template-columns:repeat(3,170px);column-gap:23px;row-gap:24px}
.card{position:relative;width:170px;height:225px;background:var(--white);box-shadow:0 1px 4px rgba(0,0,0,.12);text-align:center}
.card-shot{margin:5px;height:131px;background:
  radial-gradient(ellipse 34% 44% at 50% 50%,var(--tee) 0,var(--tee) 45%,rgba(220,237,245,0) 100%),
  linear-gradient(180deg,#e4f1f7 0%,var(--shot-bg) 100%)}
.card-cart{position:absolute;right:11px;top:11px;width:14px;height:14px;border-radius:50%;border:1px solid var(--accent);background:var(--white);display:flex;align-items:center;justify-content:center}
.card h3{margin-top:13px;font-family:'Anton',sans-serif;font-weight:400;font-size:10.5px;color:#222}
.price{margin-top:6px;font-family:'Poppins',sans-serif;font-size:9.5px;color:var(--accent)}
.card-foot{position:absolute;left:0;right:0;bottom:0;height:34px;border-top:1px solid #ececec;display:flex;align-items:center;justify-content:space-between;padding:0 22px}
.swatches{display:flex;gap:1.5px}
.swatches i{width:6px;height:6px;border-radius:50%}
.sizes{display:flex}
.sizes b{width:11px;height:9px;border:0.5px solid #cfcfcf;font-weight:400;font-size:4px;line-height:8px;color:#444}

/* promo */
.promo{position:absolute;left:0;top:1295px;width:683px;height:338px;background:var(--white)}
.promo-shirt{position:absolute;left:90px;top:55px;width:200px;height:240px;background:
  radial-gradient(ellipse 26% 22% at 52% 50%,rgba(200,200,200,.55) 0,rgba(200,200,200,0) 100%),
  radial-gradient(ellipse 50% 52% at 50% 50%,#111 0,#151515 55%,rgba(255,255,255,0) 100%)}
.promo-box{position:absolute;left:341px;top:83px;width:278px;height:164px;border:1.5px solid var(--ink);padding:14px 20px}
.promo-box .display{font-size:42px}
.promo-sub{margin-top:10px;font-family:'Poppins',sans-serif;font-weight:600;font-size:21.5px;color:var(--ink);white-space:nowrap}
.promo-box .pill{margin-top:12px;width:71px}
.chat{position:absolute;left:595px;top:1611px;width:23px;height:23px;border-radius:50%;background:var(--accent);display:flex;align-items:center;justify-content:center;z-index:1}

/* footer */
.footer{position:absolute;left:0;top:1633px;width:683px;height:217px;background:var(--footer);color:var(--footer-text)}
.footer-brand{position:absolute;left:62px;top:52px;width:86px}
.footer-brand .wordmark{color:var(--white);font-size:14px}
.social{position:absolute;left:63px;top:140px;display:flex;gap:7px}
.social i{width:24px;height:24px;border-radius:50%;border:1px solid #d8d8d8;background:#fff}
.footer-col{position:absolute;top:56px}
.footer-col h4{font-family:'Poppins',sans-serif;font-weight:500;font-size:9.5px;color:#e6e6e6;text-transform:uppercase;margin-bottom:14px}
.footer-col li{list-style:none;font-size:8px;line-height:15.6px;color:var(--footer-text)}
.contact-row{display:flex;gap:8px;font-size:8px;line-height:14px;margin-bottom:8px;color:var(--footer-text)}
.subscribe{display:flex;width:128px;height:21px;margin-bottom:20px}
.subscribe span{flex:1;background:#fff;border-radius:3px 0 0 3px;font-size:7.5px;color:#777;padding:5px 7px}
.subscribe b{width:31px;background:var(--accent);border-radius:0 3px 3px 0;display:flex;align-items:center;justify-content:center}
.cards{display:flex;gap:2px}
.cards i{width:19px;height:11px;border-radius:2px}
.copyright{position:absolute;left:0;width:683px;top:187px;text-align:center;font-size:8px;color:var(--footer-text)}

/* popup state */
.scrim{position:absolute;inset:0;background:rgba(45,50,56,.42);z-index:5}
.signup{position:absolute;left:147px;top:116px;width:390px;height:229px;background:var(--white);z-index:6;text-align:center}
.signup .display{margin-top:30px;font-size:17px}
.signup p{width:280px;margin:12px auto 0;font-size:8px;line-height:14.5px;color:var(--text)}
.signup-field{width:275px;height:25px;margin:18px auto 0;background:#e0e0e2;text-align:left;font-size:7px;color:#777;padding:8px 12px}
.signup-btn{width:275px;height:26px;margin:8px auto 0;border:1.5px solid var(--ink);font-family:'Anton',sans-serif;font-size:8.5px;line-height:23px;color:var(--ink)}
.signup-skip{margin-top:13px;font-family:'Anton',sans-serif;font-size:8.5px;color:var(--ink)}

/* standalone mark */
.board-mark{position:absolute;left:960px;top:2030px;width:370px;height:350px;display:flex;align-items:center;justify-content:center}
.board-mark .wordmark{font-size:60px;line-height:1.05}
</style>
</head>
<body>
<main class="board">

  <!-- Mobile landing -->
  <section class="screen screen--mobile" aria-label="Mobile landing page">
    <svg class="mobile-blob" width="683" height="487" viewBox="0 0 683 487" aria-hidden="true">
      <path d="M178 455 C188 330 238 250 310 232 L565 228 C600 205 640 176 683 172 L683 487 L178 487 Z" fill="var(--blob)"/>
    </svg>
    <div class="mobile-brand wordmark">Zest Crew<br>Outfitters</div>
    <div class="burger" aria-label="Menu"><span></span><span></span><span></span></div>
    <p class="mobile-kicker display">WELCOME TO</p>
    <h1 class="mobile-title display">ZEST CREW<br>OUTFITTERS</h1>
    <div class="mobile-actions">
      <span class="pill pill--solid">Zest Crew Outfitters</span>
      <span class="pill">Zest Nana</span>
    </div>
    <div class="mobile-art" role="img" aria-label="Illustration of a surfer carrying a board along a beach at sunset"></div>
    <div class="slider-bar">
      <svg width="683" height="37" viewBox="0 0 683 37" aria-hidden="true">
        <path d="M60 11 L53 18.5 L60 26" fill="none" stroke="#fff" stroke-width="1.5"/>
        <path d="M208 11 L215 18.5 L208 26" fill="none" stroke="#fff" stroke-width="1.5"/>
        <circle cx="89" cy="18.5" r="2" fill="#777"/>
        <circle cx="111" cy="18.5" r="2.5" fill="#fff"/>
        <circle cx="134" cy="18.5" r="2" fill="#777"/>
        <circle cx="156" cy="18.5" r="2" fill="#777"/>
        <circle cx="178" cy="18.5" r="2" fill="#777"/>
      </svg>
    </div>
  </section>

  <!-- Desktop home -->
  <section class="screen screen--home" aria-label="Desktop home page">
    <header class="site-header">
      <nav class="nav"><span>Home</span><span>Product</span><span>Promocode</span><span>Newsletter</span><span>Contact</span></nav>
      <div class="nav-tools">
        <svg width="10" height="10" viewBox="0 0 10 10" aria-label="Search"><circle cx="4" cy="4" r="3" fill="none" stroke="#111" stroke-width="1.6"/><path d="M6.3 6.3 L9 9" stroke="#111" stroke-width="1.8"/></svg>
        <span class="sep"></span>
        <span><svg width="14" height="12" viewBox="0 0 14 12" aria-label="Cart"><path d="M0 1 H3 L5 8 H12 L13.5 3 H4" fill="#111" stroke="#111" stroke-width="1"/><circle cx="6" cy="10.5" r="1.2" fill="#111"/><circle cx="11" cy="10.5" r="1.2" fill="#111"/></svg><sup>(0)</sup></span>
      </div>
    </header>
    <div class="brand-tab"><div class="wordmark">Zest Crew<br>Outfitters</div></div>

    <div class="hero" role="img" aria-label="Hero backdrop with a painted ocean wave and surfer">
      <h1 class="hero-title display">Zest Crew Outfitters</h1>
      <p class="hero-copy">Lorem ipsum dolor sit amet, consectetur adipiscing elit, sed do eiusmod tempor incididunt ut labore et dolore magna aliqua.</p>
      <span class="hero-cta pill">Shop Now</span>
      <div class="hero-ring"></div>
      <div class="hero-disc" role="img" aria-label="White t-shirt with a line-art surfing character"></div>
      <div class="dots" style="left:329px;top:303px"><i></i><i class="on"></i><i></i></div>
    </div>

    <section class="about">
      <h2 class="section-title display">About Us</h2>
      <p>Lorem ipsum dolor sit amet, consectetur adipiscing elit, sed do eiusmod tempor incididunt ut labore et dolore magna aliqua. Ut enim ad minim veniam, quis nostrud exercitation ullamco laboris nisi ut aliquip ex ea commodo consequat. Duis aute irure dolor in reprehenderit in voluptate velit esse cillum dolore eu fugiat nulla pariatur. Excepteur sint occaecat cupidatat non proident, sunt in culpa qui officia deserunt mollit anim id est laborum.</p>
      <span class="pill">Learn More</span>
    </section>

    <section class="products">
      <h2 class="section-title display">Our Product</h2>
      <div class="grid">
        <article class="card"><div class="card-shot" style="--tee:#111" role="img" aria-label="Black t-shirt with character print"></div><span class="card-cart"><svg width="7" height="6" viewBox="0 0 14 12"><path d="M0 1 H3 L5 8 H12 L13.5 3 H4" fill="#4f97bd"/></svg></span><h3>Product Name</h3><p class="price">$54.90</p><div class="card-foot"><span class="swatches"><i style="background:#111"></i><i style="background:#1c2a5e"></i><i style="background:#d9262e"></i><i style="background:#5ab0c9"></i><i style="background:#e6e23a"></i></span><span class="sizes"><b>S</b><b>L</b><b>M</b><b>XL</b><b>XXL</b></span></div></article>
        <article class="card"><div class="card-shot" style="--tee:#1e55c0" role="img" aria-label="Blue t-shirt with character print"></div><span class="card-cart"><svg width="7" height="6" viewBox="0 0 14 12"><path d="M0 1 H3 L5 8 H12 L13.5 3 H4" fill="#4f97bd"/></svg></span><h3>Product Name</h3><p class="price">$54.90</p><div class="card-foot"><span class="swatches"><i style="background:#111"></i><i style="background:#1c2a5e"></i><i style="background:#d9262e"></i><i style="background:#5ab0c9"></i><i style="background:#e6e23a"></i></span><span class="sizes"><b>S</b><b>L</b><b>M</b><b>XL</b><b>XXL</b></span></div></article>
        <article class="card"><div class="card-shot" style="--tee:#c01c22" role="img" aria-label="Red t-shirt with character print"></div><span class="card-cart"><svg width="7" height="6" viewBox="0 0 14 12"><path d="M0 1 H3 L5 8 H12 L13.5 3 H4" fill="#4f97bd"/></svg></span><h3>Product Name</h3><p class="price">$54.90</p><div class="card-foot"><span class="swatches"><i style="background:#111"></i><i style="background:#1c2a5e"></i><i style="background:#d9262e"></i><i style="background:#5ab0c9"></i><i style="background:#e6e23a"></i></span><span class="sizes"><b>S</b><b>L</b><b>M</b><b>XL</b><b>XXL</b></span></div></article>
        <article class="card"><div class="card-shot" style="--tee:#15203f" role="img" aria-label="Navy t-shirt with character print"></div><span class="card-cart"><svg width="7" height="6" viewBox="0 0 14 12"><path d="M0 1 H3 L5 8 H12 L13.5 3 H4" fill="#4f97bd"/></svg></span><h3>Product Name</h3><p class="price">$54.90</p><div class="card-foot"><span class="swatches"><i style="background:#111"></i><i style="background:#1c2a5e"></i><i style="background:#d9262e"></i><i style="background:#5ab0c9"></i><i style="background:#e6e23a"></i></span><span class="sizes"><b>S</b><b>L</b><b>M</b><b>XL</b><b>XXL</b></span></div></article>
        <article class="card"><div class="card-shot" style="--tee:#a9a9a9" role="img" aria-label="Grey t-shirt with character print"></div><span class="card-cart"><svg width="7" height="6" viewBox="0 0 14 12"><path d="M0 1 H3 L5 8 H12 L13.5 3 H4" fill="#4f97bd"/></svg></span><h3>Product Name</h3><p class="price">$54.90</p><div class="card-foot"><span class="swatches"><i style="background:#111"></i><i style="background:#1c2a5e"></i><i style="background:#d9262e"></i><i style="background:#5ab0c9"></i><i style="background:#e6e23a"></i></span><span class="sizes"><b>S</b><b>L</b><b>M</b><b>XL</b><b>XXL</b></span></div></article>
        <article class="card"><div class="card-shot" style="--tee:#e3c81e" role="img" aria-label="Yellow t-shirt with character print"></div><span class="card-cart"><svg width="7" height="6" viewBox="0 0 14 12"><path d="M0 1 H3 L5 8 H12 L13.5 3 H4" fill="#4f97bd"/></svg></span><h3>Product Name</h3><p class="price">$54.90</p><div class="card-foot"><span class="swatches"><i style="background:#111"></i><i style="background:#1c2a5e"></i><i style="background:#d9262e"></i><i style="background:#5ab0c9"></i><i style="background:#e6e23a"></i></span><span class="sizes"><b>S</b><b>L</b><b>M</b><b>XL</b><b>XXL</b></span></div></article>
      </div>
    </section>

    <section class="promo">
      <div class="promo-shirt" role="img" aria-label="Black t-shirt with the brand character print"></div>
      <div class="promo-box">
        <p class="display">SAVE $50</p>
        <p class="promo-sub">On Your First Order</p>
        <span class="pill">Order Now</span>
      </div>
    </section>
    <span class="chat" aria-label="Chat support"><svg width="11" height="9" viewBox="0 0 11 9"><ellipse cx="5.5" cy="4" rx="5" ry="3.6" fill="#fff"/><path d="M2 6.5 L1 9 L4.5 7" fill="#fff"/></svg></span>

    <footer class="footer">
      <div class="footer-brand"><div class="wordmark">Zest Crew<br>Outfitters</div></div>
      <div class="social"><i></i><i></i><i></i><i></i></div>
      <div class="footer-col" style="left:215px"><h4>Quick Links</h4><ul><li>Home</li><li>Product</li><li>Promocode</li><li>Newsletter</li><li>Contact</li></ul></div>
      <div class="footer-col" style="left:325px"><h4>Contact Us</h4>
        <div class="contact-row"><svg width="9" height="11" viewBox="0 0 9 11"><path d="M4.5 0 C7 0 9 2 9 4.3 C9 7 4.5 11 4.5 11 C4.5 11 0 7 0 4.3 C0 2 2 0 4.5 0Z" fill="#ccc"/><circle cx="4.5" cy="4.2" r="1.6" fill="#000"/></svg><span>Lorem ipsum dolor sit<br>amet, consectetur</span></div>
        <div class="contact-row"><svg width="10" height="10" viewBox="0 0 10 10"><path d="M2 0 L4 2.5 L3 4 C4 6 5 7 6.5 7.5 L8 6.5 L10 8.5 L8.5 10 C4 9.5 0.5 6 0 1.5Z" fill="#ccc"/></svg><span>+1 (888) 888 8888</span></div>
        <div class="contact-row"><svg width="10" height="8" viewBox="0 0 10 8"><rect width="10" height="8" fill="#ccc"/><path d="M0 0 L5 4.5 L10 0" fill="none" stroke="#000"/></svg><span>info@zestcrewoutfitters.com</span></div>
      </div>
      <div class="footer-col" style="left:491px"><h4>Newsletter</h4>
        <div class="subscribe"><span>Enter email</span><b><svg width="9" height="7" viewBox="0 0 10 8"><rect width="10" height="8" fill="#fff"/><path d="M0 0 L5 4.5 L10 0" fill="none" stroke="#6aaed0"/></svg></b></div>
        <h4>Payment Option</h4>
        <div class="cards"><i style="background:#d8d8d8"></i><i style="background:#e8eef8"></i><i style="background:#ffffff"></i><i style="background:#dfe3ea"></i><i style="background:#3f8fd6"></i><i style="background:#f0d8d0"></i></div>
      </div>
      <p class="copyright">©Copyrights 2022 Zest Crew Outfitters &nbsp;|&nbsp; All Rights Reserved</p>
    </footer>
  </section>

  <!-- Desktop home with newsletter sign-up open -->
  <section class="screen screen--popup" aria-label="Desktop home page with newsletter sign-up">
    <header class="site-header">
      <nav class="nav"><span>Home</span><span>Product</span><span>Promocode</span><span>Newsletter</span><span>Contact</span></nav>
      <div class="nav-tools">
        <svg width="10" height="10" viewBox="0 0 10 10" aria-label="Search"><circle cx="4" cy="4" r="3" fill="none" stroke="#111" stroke-width="1.6"/><path d="M6.3 6.3 L9 9" stroke="#111" stroke-width="1.8"/></svg>
        <span class="sep"></span>
        <span><svg width="14" height="12" viewBox="0 0 14 12" aria-label="Cart"><path d="M0 1 H3 L5 8 H12 L13.5 3 H4" fill="#111" stroke="#111" stroke-width="1"/><circle cx="6" cy="10.5" r="1.2" fill="#111"/><circle cx="11" cy="10.5" r="1.2" fill="#111"/></svg><sup>(0)</sup></span>
      </div>
    </header>
    <div class="brand-tab"><div class="wordmark">Zest Crew<br>Outfitters</div></div>

    <div class="hero" role="img" aria-label="Hero backdrop with a painted ocean wave and surfer">
      <h1 class="hero-title display">Zest Crew Outfitters</h1>
      <p class="hero-copy">Lorem ipsum dolor sit amet, consectetur adipiscing elit, sed do eiusmod tempor incididunt ut labore et dolore magna aliqua.</p>
      <span class="hero-cta pill">Shop Now</span>
      <div class="hero-ring"></div>
      <div class="hero-disc" role="img" aria-label="White t-shirt with a line-art surfing character"></div>
      <div class="dots" style="left:329px;top:303px"><i></i><i class="on"></i><i></i></div>
    </div>

    <section class="about">
      <h2 class="section-title display">About Us</h2>
      <p>Lorem ipsum dolor sit amet, consectetur adipiscing elit, sed do eiusmod tempor incididunt ut labore et dolore magna aliqua. Ut enim ad minim veniam, quis nostrud exercitation ullamco laboris nisi ut aliquip ex ea commodo consequat. Duis aute irure dolor in reprehenderit in voluptate velit esse cillum dolore eu fugiat nulla pariatur. Excepteur sint occaecat cupidatat non proident, sunt in culpa qui officia deserunt mollit anim id est laborum.</p>
      <span class="pill">Learn More</span>
    </section>

    <section class="products">
      <h2 class="section-title display">Our Product</h2>
      <div class="grid">
        <article class="card"><div class="card-shot" style="--tee:#111" role="img" aria-label="Black t-shirt with character print"></div><span class="card-cart"><svg width="7" height="6" viewBox="0 0 14 12"><path d="M0 1 H3 L5 8 H12 L13.5 3 H4" fill="#4f97bd"/></svg></span><h3>Product Name</h3><p class="price">$54.90</p><div class="card-foot"><span class="swatches"><i style="background:#111"></i><i style="background:#1c2a5e"></i><i style="background:#d9262e"></i><i style="background:#5ab0c9"></i><i style="background:#e6e23a"></i></span><span class="sizes"><b>S</b><b>L</b><b>M</b><b>XL</b><b>XXL</b></span></div></article>
        <article class="card"><div class="card-shot" style="--tee:#1e55c0" role="img" aria-label="Blue t-shirt with character print"></div><span class="card-cart"><svg width="7" height="6" viewBox="0 0 14 12"><path d="M0 1 H3 L5 8 H12 L13.5 3 H4" fill="#4f97bd"/></svg></span><h3>Product Name</h3><p class="price">$54.90</p><div class="card-foot"><span class="swatches"><i style="background:#111"></i><i style="background:#1c2a5e"></i><i style="background:#d9262e"></i><i style="background:#5ab0c9"></i><i style="background:#e6e23a"></i></span><span class="sizes"><b>S</b><b>L</b><b>M</b><b>XL</b><b>XXL</b></span></div></article>
        <article class="card"><div class="card-shot" style="--tee:#c01c22" role="img" aria-label="Red t-shirt with character print"></div><span class="card-cart"><svg width="7" height="6" viewBox="0 0 14 12"><path d="M0 1 H3 L5 8 H12 L13.5 3 H4" fill="#4f97bd"/></svg></span><h3>Product Name</h3><p class="price">$54.90</p><div class="card-foot"><span class="swatches"><i style="background:#111"></i><i style="background:#1c2a5e"></i><i style="background:#d9262e"></i><i style="background:#5ab0c9"></i><i style="background:#e6e23a"></i></span><span class="sizes"><b>S</b><b>L</b><b>M</b><b>XL</b><b>XXL</b></span></div></article>
        <article class="card"><div class="card-shot" style="--tee:#15203f" role="img" aria-label="Navy t-shirt with character print"></div><span class="card-cart"><svg width="7" height="6" viewBox="0 0 14 12"><path d="M0 1 H3 L5 8 H12 L13.5 3 H4" fill="#4f97bd"/></svg></span><h3>Product Name</h3><p class="price">$54.90</p><div class="card-foot"><span class="swatches"><i style="background:#111"></i><i style="background:#1c2a5e"></i><i style="background:#d9262e"></i><i style="background:#5ab0c9"></i><i style="background:#e6e23a"></i></span><span class="sizes"><b>S</b><b>L</b><b>M</b><b>XL</b><b>XXL</b></span></div></article>
        <article class="card"><div class="card-shot" style="--tee:#a9a9a9" role="img" aria-label="Grey t-shirt with character print"></div><span class="card-cart"><svg width="7" height="6" viewBox="0 0 14 12"><path d="M0 1 H3 L5 8 H12 L13.5 3 H4" fill="#4f97bd"/></svg></span><h3>Product Name</h3><p class="price">$54.90</p><div class="card-foot"><span class="swatches"><i style="background:#111"></i><i style="background:#1c2a5e"></i><i style="background:#d9262e"></i><i style="background:#5ab0c9"></i><i style="background:#e6e23a"></i></span><span class="sizes"><b>S</b><b>L</b><b>M</b><b>XL</b><b>XXL</b></span></div></article>
        <article class="card"><div class="card-shot" style="--tee:#e3c81e" role="img" aria-label="Yellow t-shirt with character print"></div><span class="card-cart"><svg width="7" height="6" viewBox="0 0 14 12"><path d="M0 1 H3 L5 8 H12 L13.5 3 H4" fill="#4f97bd"/></svg></span><h3>Product Name</h3><p class="price">$54.90</p><div class="card-foot"><span class="swatches"><i style="background:#111"></i><i style="background:#1c2a5e"></i><i style="background:#d9262e"></i><i style="background:#5ab0c9"></i><i style="background:#e6e23a"></i></span><span class="sizes"><b>S</b><b>L</b><b>M</b><b>XL</b><b>XXL</b></span></div></article>
      </div>
    </section>

    <section class="promo">
      <div class="promo-shirt" role="img" aria-label="Black t-shirt with the brand character print"></div>
      <div class="promo-box">
        <p class="display">SAVE $50</p>
        <p class="promo-sub">On Your First Order</p>
        <span class="pill">Order Now</span>
      </div>
    </section>
    <span class="chat" aria-label="Chat support"><svg width="11" height="9" viewBox="0 0 11 9"><ellipse cx="5.5" cy="4" rx="5" ry="3.6" fill="#fff"/><path d="M2 6.5 L1 9 L4.5 7" fill="#fff"/></svg></span>

    <footer class="footer">
      <div class="footer-brand"><div class="wordmark">Zest Crew<br>Outfitters</div></div>
      <div class="social"><i></i><i></i><i></i><i></i></div>
      <div class="footer-col" style="left:215px"><h4>Quick Links</h4><ul><li>Home</li><li>Product</li><li>Promocode</li><li>Newsletter</li><li>Contact</li></ul></div>
      <div class="footer-col" style="left:325px"><h4>Contact Us</h4>
        <div class="contact-row"><svg width="9" height="11" viewBox="0 0 9 11"><path d="M4.5 0 C7 0 9 2 9 4.3 C9 7 4.5 11 4.5 11 C4.5 11 0 7 0 4.3 C0 2 2 0 4.5 0Z" fill="#ccc"/><circle cx="4.5" cy="4.2" r="1.6" fill="#000"/></svg><span>Lorem ipsum dolor sit<br>amet, consectetur</span></div>
        <div class="contact-row"><svg width="10" height="10" viewBox="0 0 10 10"><path d="M2 0 L4 2.5 L3 4 C4 6 5 7 6.5 7.5 L8 6.5 L10 8.5 L8.5 10 C4 9.5 0.5 6 0 1.5Z" fill="#ccc"/></svg><span>+1 (888) 888 8888</span></div>
        <div class="contact-row"><svg width="10" height="8" viewBox="0 0 10 8"><rect width="10" height="8" fill="#ccc"/><path d="M0 0 L5 4.5 L10 0" fill="none" stroke="#000"/></svg><span>info@zestcrewoutfitters.com</span></div>
      </div>
      <div class="footer-col" style="left:491px"><h4>Newsletter</h4>
        <div class="subscribe"><span>Enter email</span><b><svg width="9" height="7" viewBox="0 0 10 8"><rect width="10" height="8" fill="#fff"/><path d="M0 0 L5 4.5 L10 0" fill="none" stroke="#6aaed0"/></svg></b></div>
        <h4>Payment Option</h4>
        <div class="cards"><i style="background:#d8d8d8"></i><i style="background:#e8eef8"></i><i style="background:#ffffff"></i><i style="background:#dfe3ea"></i><i style="background:#3f8fd6"></i><i style="background:#f0d8d0"></i></div>
      </div>
      <p class="copyright">©Copyrights 2022 Zest Crew Outfitters &nbsp;|&nbsp; All Rights Reserved</p>
    </footer>

    <div class="scrim"></div>
    <div class="signup" role="dialog" aria-label="Newsletter sign-up">
      <h2 class="display">Get In Touch</h2>
      <p>Lorem ipsum dolor sit amet, consectetur adipiscing elit, sed do eiusmod tempor incididunt ut labore et dolore magna aliqua.</p>
      <div class="signup-field">Email</div>
      <div class="signup-btn">Subscribe</div>
      <div class="signup-skip">No Thanks</div>
    </div>
  </section>

  <!-- Brand mark -->
  <div class="board-mark"><div class="wordmark">Zest Crew<br>Outfitters</div></div>

</main>
</body>
</html>
```